Roofing web site brvt roofing

Look at some of our competitors web page we like something similar with NYC roofing
https://www.quillbarroofing.example/
Maybe a skyline picture of nyc at the home page with a picture of flat roofing installation

Target Market(s)

Commercial and residential flat roofs

Industry/Entity Type

Flat Roofing industry

Coding

Coded - Design and coding required

Number of Pages Required

2 page

Font styles to use
Decorative
Script

Colors

Designer to choose colors to be used in the design.

Requirements
Must have
• At BRVT Roofing, we are a trusted and reputable roofing company specializing in new construction flat roof installation and repair. With years of experience in the industry, we take pride in providing exceptional roofing solutions to our valued clients. Our team of highly skilled and dedicated roofing professionals understands the unique challenges and requirements of new construction projects. We work closely with builders, contractors, and architects to design and install flat roofs that meet the specific needs of each project. From commercial buildings to residential complexes, we have the expertise to deliver reliable and durable roofing solutions. When it comes to flat roof repairs, we are your go-to experts. Our experienced technicians conduct thorough inspections to identify the root cause of any issues your roof may be experiencing. We utilize the latest industry techniques and high-quality materials to efficiently repair your flat roof, ensuring its integrity and longevity. At BRVT Roofing, we prioritize customer satisfaction above all else. We believe in building strong relationships with our clients by providing exceptional craftsmanship and outstanding customer service. Our team is dedicated to delivering projects on time, within budget, and to the highest standards of quality. We understand that a well-maintained roof is essential for protecting your property and ensuring the safety of its occupants. That's why we use only the best materials and employ skilled professionals who are trained in the latest roofing practices. Our commitment to excellence is evident in every project we undertake. As a fully licensed and insured roofing company, we prioritize safety and adhere to industry regulations and best practices. We take every precaution to create a safe working environment for our team and minimize any disruptions to your daily routine. When you choose BRVT Roofing, you can trust that you are working with a reliable and reputable company that will deliver exceptional results. We are committed to exceeding your expectations and providing you with a roof that is built to last. Contact us today for all your new construction flat roof installation and repair needs.
Nice to have
• NYC skyline background with commercial roofing pictures of torching roofing

```html
<!DOCTYPE html>
<html lang="en">
<head>
<meta charset="utf-8">
<title>BRVT Roofing – Home and About proposal</title>
<link href="https://fonts.googleapis.com/css2?family=Roboto:wght@400;500;700&display=swap" rel="stylesheet">
<style>
:root{
  --navy:#050b18;
  --blue:#1688f5;
  --white:#ffffff;
  --ink:#0b0d12;
  --muted:#c9ced8;
  --line:#2a3142;
  --board:#ffffff;
}
*{box-sizing:border-box;margin:0;padding:0}
html,body{width:754px;height:1200px;overflow:hidden;background:var(--board)}
body{position:relative;font-family:'Roboto',sans-serif;color:var(--ink)}
.page{position:absolute;width:359px;box-shadow:0 0 3px rgba(0,0,0,.15)}
.page-home{left:14px;top:18px}
.page-about{left:381px;top:189px}
.sec{position:relative;width:359px;overflow:hidden}
.dark{background:var(--navy);color:var(--white)}
.light{background:var(--white);color:var(--ink)}
.abs{position:absolute}
.label{font-size:3.6px;color:var(--blue);font-weight:500}
.center{text-align:center}
.btn{position:absolute;display:flex;align-items:center;justify-content:center;font-size:3.6px;height:11px;background:var(--blue);color:#fff}
.btn-ghost{background:transparent;border:.5px solid #fff}
.link{position:absolute;font-size:3.6px;display:flex;align-items:center;gap:2px}
.photo{position:absolute}
.body{font-size:3.7px;line-height:1.5}
.brand{font-size:4px;font-weight:500}
.brand b{font-weight:500}

/* nav */
.nav{height:18px}
.nav-links{position:absolute;left:16px;top:7px;display:flex;gap:8px;font-size:3.6px}
.nav-links .active{color:var(--blue)}
.nav .brand{position:absolute;left:168px;top:7px}
.nav-phone{position:absolute;left:264px;top:6.6px;font-size:3.8px;display:flex;gap:2px;align-items:center}

/* hero */
.hero{height:224px}
.hero .photo{inset:0;background:linear-gradient(160deg,#3f3a33 0%,#7a6344 35%,#4d4741 60%,#6c6a63 100%)}
.hero-shade{position:absolute;inset:0;background:rgba(10,12,20,.35)}
.hero h1{position:absolute;left:0;right:0;top:64px;font-size:14px;line-height:1.2;font-weight:500;color:#fff;text-align:center}
.hero p{position:absolute;left:84px;width:191px;top:104px;font-size:4.2px;line-height:1.6;color:#fff;text-align:center}

/* services */
.services{height:167px}
.services h2{position:absolute;left:16px;top:36px;font-size:11.5px;line-height:1.25;font-weight:500}
.svc-col{position:absolute;width:86px;top:58px}
.svc-col h3{font-size:4.4px;font-weight:500;margin:4px 0 4px}
.svc-col p{font-size:3.6px;line-height:1.55;color:var(--muted)}

/* process */
.process{height:270px}
.process h2{position:absolute;left:0;right:0;top:37px;font-size:11.5px;line-height:1.25;font-weight:500}
.card{position:absolute;top:112px;width:101px;text-align:center}
.card .photo{position:relative;width:101px;height:60px}
.card h3{font-size:7.6px;font-weight:500;margin:8px 0 6px}
.card p{font-size:3.6px;line-height:1.55}

/* testimonials */
.testi{height:164px}
.testi h2{position:absolute;left:0;right:0;top:27px;font-size:11.5px;font-weight:500}
.quote{position:absolute;top:78px;width:90px;text-align:center}
.quote p{font-size:4.4px;font-weight:500;line-height:1.55}
.quote span{display:block;margin-top:9px;font-size:3.6px;font-weight:500}
.round{position:absolute;width:12px;height:12px;border-radius:50%;border:.6px solid currentColor;display:flex;align-items:center;justify-content:center}
.dots{position:absolute;left:0;right:0;display:flex;justify-content:center;gap:2.6px}
.dots i{width:1.8px;height:1.8px;border-radius:50%;background:#9aa0ab;display:block}
.dots i.on{background:var(--blue)}

/* gallery */
.gallery{height:281px}
.gallery h2{position:absolute;left:0;right:0;top:27px;font-size:11.5px;font-weight:500}
.round-solid{background:#fff;color:#111;border-color:#555}

/* note */
.note{position:absolute;left:391px;top:18px;width:330px;font-size:7.5px;line-height:1.5;color:#111}
.note p{margin-bottom:7px}

/* about */
.about{height:393px}
.about h2{position:absolute;left:0;right:0;top:37px;font-size:11.5px;line-height:1.25;font-weight:500}
.tri{position:absolute;top:124px;width:108px;text-align:center}
.tri h3{font-size:4.4px;font-weight:500;margin-bottom:2px}
.tri p{font-size:3.5px;line-height:1.55;color:var(--muted)}

/* team */
.team{height:185px}
.member{position:absolute;top:85px}
.member .photo{position:relative;width:74px;height:72px}
.member-info{position:absolute;left:82px;top:0;width:90px}
.member-info h3{font-size:4.4px;font-weight:500}
.member-info .role{font-size:4px;margin:2px 0 4px}
.member-info p{font-size:3.5px;line-height:1.55}
.social{display:flex;gap:4px;margin-top:6px}

/* contact */
.contact{height:348px}
.field{position:absolute;left:16px;width:154px}
.field label{display:block;font-size:3.6px;margin-bottom:2px}
.field div{height:12px;background:#fff;border:.6px solid var(--blue)}
.info{position:absolute;width:80px}
.info h3{font-size:4.6px;font-weight:500;margin:3px 0 2px}
.info p{font-size:3.6px;line-height:1.5}
.info a{font-size:3.6px;color:var(--blue);text-decoration:underline}
.footer-links{position:absolute;left:121px;top:292px;display:flex;gap:8px;font-size:3.6px}
</style>
</head>
<body>

<!-- Home page -->
<div class="page page-home">
  <section class="sec dark nav">
    <nav class="nav-links"><span class="active">HOME</span><span>FLAT ROOF INSTALLATION</span><span>ROOF REPAIR</span><span>ABOUT US</span></nav>
    <div class="brand">BRVT Roofing</div>
    <div class="nav-phone">
      <svg width="4" height="4" viewBox="0 0 24 24" fill="none" stroke="#fff" stroke-width="2.4"><path d="M22 17v3a2 2 0 0 1-2 2A19 19 0 0 1 2 4a2 2 0 0 1 2-2h3l2 5-2.5 1.5a11 11 0 0 0 5 5L13 11l5 2z"/></svg>555-014-2290
    </div>
    <div class="btn" style="left:313px;top:4px;width:30px;height:10px">Free Quote</div>
  </section>

  <section class="sec hero">
    <div class="photo" role="img" aria-label="Roofer laying decking on a pitched roof above a suburban street"></div>
    <div class="hero-shade"></div>
    <h1>Expert Roofing Solutions<br>Tailored to Your Project</h1>
    <p>Welcome to BRVT Roofing, where excellence meets innovation in roofing solutions. Our seasoned team collaborates seamlessly with builders, contractors, and architects to design and implement flat roofs uniquely tailored to the specific needs of your project. With a commitment to quality and precision, we take pride in delivering top-notch roofing solutions that stand the test of time.</p>
    <div class="btn" style="left:141px;top:148px;width:42px">Get a Free Quote</div>
    <div class="btn btn-ghost" style="left:187px;top:148px;width:32px">Contact Us</div>
  </section>

  <section class="sec dark services">
    <div class="label abs" style="left:16px;top:29px">Services</div>
    <h2>Comprehensive<br>Roofing Services<br>Tailored to Your Needs</h2>
    <p class="body abs" style="left:163px;top:28px;width:180px;font-size:3.8px">Narrow down your project with BRVT Roofing's expert services. From tailored flat roof installations to meticulous repairs, we deliver top-notch solutions. Trust in quality craftsmanship for lasting roofing excellence.</p>
    <div class="svc-col" style="left:163px">
      <svg width="11" height="10" viewBox="0 0 24 22" fill="none" stroke="#1688f5" stroke-width="2"><path d="M3 11 12 3l9 8M6 9v11h12V9"/><rect x="10" y="13" width="4" height="4"/></svg>
      <h3>Flat Roof Installation Expertise</h3>
      <p>Experience superior craftsmanship with our Flat Roof Installation service. Tailored to your project's needs, our skilled team ensures precision and durability in every detail, delivering roofing solutions that stand the test of time.</p>
    </div>
    <div class="svc-col" style="left:256px">
      <svg width="11" height="10" viewBox="0 0 24 22" fill="none" stroke="#1688f5" stroke-width="2"><path d="M2 20V9l8-6 8 6M18 20V5h4v15M2 20h20"/><path d="M6 12h3v3H6zM12 12h3v3h-3z"/></svg>
      <h3>Precision Roof Repair Solutions</h3>
      <p>Trust our expert team for Precision Roof Repair solutions. Meticulous in every detail, we deliver repairs that enhance durability and safeguard your investment, ensuring a resilient and long-lasting roof.</p>
    </div>
    <div class="btn" style="left:163px;top:126px;width:41px">Get a Free Quote</div>
    <div class="link" style="left:210px;top:129px;color:var(--blue)">Learn More <span>›</span></div>
  </section>

  <section class="sec light process">
    <div class="label abs center" style="left:0;right:0;top:29px">Trustworthy</div>
    <h2 class="center">Our Collaborative Process with<br>Builders, Contractors, and Architects</h2>
    <p class="body abs center" style="left:85px;width:190px;top:73px">At BRVT Roofing, we believe in a collaborative approach to roofing projects. From consultation to project completion, we work closely with builders, contractors, and architects to ensure the best possible results.</p>
    <div class="card" style="left:16px">
      <div class="photo" role="img" aria-label="Two colleagues planning a project at a laptop" style="background:linear-gradient(135deg,#d9d7d0,#9fa39c)"></div>
      <h3>Consultation and Planning</h3>
      <p>We start by conducting a thorough consultation to understand your roofing needs and project requirements.</p>
    </div>
    <div class="card" style="left:129px">
      <div class="photo" role="img" aria-label="Roofer in a hi-vis shirt working on a shingle roof under trees" style="background:linear-gradient(180deg,#5b86c0,#4b5a3c 55%,#3a3a3c)"></div>
      <h3>Design and Implementation</h3>
      <p>Our experienced team collaborates with builders, contractors, and architects to design and implement flat roofs tailored to your project's unique needs.</p>
    </div>
    <div class="card" style="left:242px">
      <div class="photo" role="img" aria-label="Gloved hands fastening a metal roof panel" style="background:linear-gradient(135deg,#7fb2a8,#a48a6a 55%,#e3b52e)"></div>
      <h3>Reliable and Durable</h3>
      <p>We ensure reliable and durable roofing solutions for both commercial and residential projects.</p>
    </div>
    <div class="btn" style="left:142px;top:226px;width:42px">Get a Free Quote</div>
    <div class="link" style="left:189px;top:229px">Contact Us <span>›</span></div>
  </section>

  <section class="sec dark testi">
    <h2 class="center">Testimonials That Tell Our Story</h2>
    <p class="body abs center" style="left:0;right:0;top:50px">Client voices echo satisfaction—our commitment to roofing excellence.</p>
    <div class="round" style="left:16px;top:89px;font-size:6px">←</div>
    <div class="quote" style="left:38px"><p>"Exceptional service and attention to detail. BRVT Roofing surpassed our expectations, ensuring a flawless flat roof installation. Highly recommended."</p><span>Paul Avery</span></div>
    <div class="quote" style="left:135px"><p>"Fast and efficient roof repair services. BRVT Roofing's dedication to quality and customer satisfaction is outstanding. A reliable choice."</p><span>Grace Holloway</span></div>
    <div class="quote" style="left:233px"><p>"On-time delivery, within budget. The skilled craftsmanship in our flat roof installation speaks volumes. BRVT Roofing is a trustworthy partner."</p><span>Martin Keel</span></div>
    <div class="round" style="left:331px;top:89px;font-size:6px">→</div>
    <div class="dots" style="top:130px"><i class="on"></i><i></i><i></i><i></i><i></i></div>
  </section>

  <section class="sec light gallery">
    <h2 class="center">Project Gallery</h2>
    <p class="body abs center" style="left:0;right:0;top:50px">Showcasing Our Roofing Mastery</p>
    <div class="photo" role="img" aria-label="Roofer with a nail gun on a shingle roof against blue sky" style="left:16px;top:75px;width:160px;height:160px;background:linear-gradient(180deg,#9cc8ea 0%,#b4cfe0 35%,#4f4f52 60%,#3d3d40 100%)"></div>
    <div class="photo" role="img" aria-label="Timber battens and insulation over a flat roof deck" style="left:184px;top:75px;width:160px;height:160px;background:linear-gradient(180deg,#1f5e9c 0%,#b89a5a 40%,#6f7478 70%,#2b2b2d 100%)"></div>
    <div class="photo" role="img" aria-label="Next gallery photo" style="left:351px;top:75px;width:8px;height:160px;background:#8a5a4a"></div>
    <div class="round round-solid" style="left:9px;top:149px;font-size:6px">←</div>
    <div class="round round-solid" style="left:337px;top:149px;font-size:6px">→</div>
    <div class="dots" style="top:252px"><i style="background:#111"></i><i style="background:#ccc"></i><i style="background:#ccc"></i><i style="background:#ccc"></i><i style="background:#ccc"></i></div>
  </section>
</div>

<!-- Proposal note -->
<div class="note">
  <p>Hi, please find my proposal attached. I have change your original colours to better match the style I went for. Which is modern and focused on getting more potential leads for your business.<br>This is the Home page design, which is mobile responsive and should you like the proposal, we will develop three more pages, one for each service and optional About Us Page, though most of the info is on the home page.</p>
  <p>The images are placeholders, so we can easily change those, like the Team members for example, having faces will improve trust in your business and therefore increase conversion.</p>
  <p>I'm looking forward to hear your feedback and work on any desired improvement or different colours schemes.</p>
  <p>Kind regards.</p>
</div>

<!-- About page -->
<div class="page page-about">
  <section class="sec dark about">
    <div class="label abs center" style="left:0;right:0;top:29px">About Us</div>
    <h2 class="center">Unveiling the Essence of BRVT<br>Roofing: Our Story</h2>
    <p class="body abs center" style="left:84px;width:192px;top:73px">At BRVT Roofing, our story is one of dedication, expertise, and unwavering commitment. Founded on a passion for superior roofing solutions, our journey unfolds with a skilled team, a history of excellence, and a values-driven approach. Discover the essence of BRVT Roofing and the values that guide us in every project we undertake.</p>
    <div class="tri" style="left:16px;padding-bottom:4px;border-bottom:.8px solid var(--blue)"><h3 style="color:var(--blue)">Our Mission</h3><p>Dedicated to setting new standards in roofing excellence, our mission at BRVT Roofing is to deliver unparalleled craftsmanship and customer satisfaction. With each project, we strive to exceed expectations, ensuring roofs that stand the test of time.</p></div>
    <div class="tri" style="left:125px"><h3>Our Team</h3><p>Meet the heart of BRVT Roofing—our dedicated team of skilled professionals. With a wealth of experience and a passion for precision, we collaborate to bring your roofing visions to life. Together, we uphold the values that define our commitment to excellence.</p></div>
    <div class="tri" style="left:235px"><h3>Our Values</h3><p>Integrity, quality, and customer-centricity. We pride ourselves on transparency, ethical practices, and a relentless pursuit of perfection. With us, your roofing project is not just a task but a commitment to lasting quality and satisfaction.</p></div>
    <div class="photo" role="img" aria-label="Roofer in a hard hat unrolling membrane on a flat roof" style="left:16px;top:181px;width:327px;height:184px;background:linear-gradient(180deg,#c7ccc2 0%,#9aa08f 30%,#7a7c7a 55%,#595b5c 100%)"></div>
  </section>

  <section class="sec light team">
    <div class="label abs" style="left:16px;top:29px">Expertise</div>
    <h2 class="abs" style="left:16px;top:37px;font-size:12px;font-weight:500">Our team</h2>
    <p class="body abs" style="left:16px;top:58px">Lorem ipsum dolor sit amet, consectetur adipiscing elit.</p>
    <div class="member" style="left:16px">
      <div class="photo" role="img" aria-label="Portrait of the project leader" style="background:linear-gradient(180deg,#c9d4dc,#5a6470)"></div>
      <div class="member-info"><h3>Owen R</h3><div class="role">Project Leader</div><p>Owen is Victor's right hand man. He's all about structure and organization. Through general oversight, his focus is to bring your job to completion on time and within budget.</p>
        <div class="social"><svg width="5" height="5"><rect width="5" height="5" fill="#111"/></svg><svg width="5" height="5"><rect width="5" height="5" fill="#111"/></svg><svg width="5" height="5"><circle cx="2.5" cy="2.5" r="2.5" fill="#111"/></svg></div></div>
    </div>
    <div class="member" style="left:187px">
      <div class="photo" role="img" aria-label="Portrait of the business manager" style="background:linear-gradient(90deg,#e08a3e,#c9793a 60%,#8a8c8c)"></div>
      <div class="member-info"><h3>Nadia P</h3><div class="role">Business Manager &amp; Development</div><p>Victor's daughter Nadia has been around the business since she was a kid. With a degree in Green Construction, she incorporates the latest in green options into your project. Saving the planet, while saving you money, is her goal!</p>
        <div class="social"><svg width="5" height="5"><rect width="5" height="5" fill="#111"/></svg><svg width="5" height="5"><rect width="5" height="5" fill="#111"/></svg><svg width="5" height="5"><circle cx="2.5" cy="2.5" r="2.5" fill="#111"/></svg></div></div>
    </div>
  </section>

  <section class="sec dark contact">
    <div class="label abs" style="left:16px;top:29px">Inquire</div>
    <h2 class="abs" style="left:16px;top:37px;font-size:12px;font-weight:500">Contact us</h2>
    <p class="body abs" style="left:16px;top:58px">Contact us for detailed information, request a free quote or other enquiries.</p>
    <div class="field" style="top:78px"><label>Name</label><div></div></div>
    <div class="field" style="top:104px"><label>Email</label><div></div></div>
    <div class="field" style="top:130px"><label>Phone Number</label><div></div></div>
    <div class="field" style="top:156px"><label>Message</label><div style="height:45px;font-size:3.4px;color:#888;padding:3px">Type your message...</div></div>
    <div class="abs" style="left:16px;top:216px;font-size:3.4px;display:flex;align-items:center;gap:2px"><span style="width:4.5px;height:4.5px;background:#fff;display:inline-block"></span>I accept the <span style="color:var(--blue);text-decoration:underline">Terms</span></div>
    <div class="btn" style="left:16px;top:229px;width:25px;height:12px">Submit</div>
    <div class="info" style="left:189px;top:78px">
      <svg width="7" height="6" viewBox="0 0 24 20" fill="none" stroke="#1688f5" stroke-width="2.4"><rect x="2" y="2" width="20" height="16"/><path d="m2 3 10 8 10-8"/></svg>
      <h3>Email</h3><p>You can directly email us.</p><a>hello@brvtroofing.example</a>
    </div>
    <div class="info" style="left:269px;top:78px">
      <svg width="6" height="6" viewBox="0 0 24 24" fill="none" stroke="#1688f5" stroke-width="2.4"><path d="M22 17v3a2 2 0 0 1-2 2A19 19 0 0 1 2 4a2 2 0 0 1 2-2h3l2 5-2.5 1.5a11 11 0 0 0 5 5L13 11l5 2z"/></svg>
      <h3>Phone</h3><p>Still got questions?.</p><a>555-014-2290</a>
    </div>
    <div class="info" style="left:189px;top:122px">
      <svg width="6" height="7" viewBox="0 0 24 28" fill="none" stroke="#1688f5" stroke-width="2.4"><path d="M12 26s9-8 9-15a9 9 0 0 0-18 0c0 7 9 15 9 15z"/><circle cx="12" cy="11" r="3"/></svg>
      <h3>Office</h3><p>48 Harbor Lane, Queens NY<br>11101</p>
      <div style="font-size:3.6px;color:var(--blue);margin-top:6px">Get Directions ›</div>
    </div>
    <div class="brand abs" style="left:16px;top:292px;font-size:3.8px">BRVT Roofing</div>
    <div class="footer-links"><span>Home</span><span>Flat Roof Installation</span><span>Roof Repair</span><span>About Us</span></div>
    <div class="abs" style="left:303px;top:292px;display:flex;gap:4px">
      <svg width="5" height="5"><circle cx="2.5" cy="2.5" r="2.5" fill="#1688f5"/></svg><svg width="5" height="5"><circle cx="2.5" cy="2.5" r="2.5" fill="#1688f5"/></svg><svg width="5" height="5"><circle cx="2.5" cy="2.5" r="2.5" fill="#1688f5"/></svg><svg width="5" height="5"><rect width="5" height="5" fill="#1688f5"/></svg><svg width="5" height="5"><rect width="5" height="5" fill="#1688f5"/></svg>
    </div>
    <div class="abs" style="left:16px;right:16px;top:313px;border-top:.5px solid #6a7080"></div>
    <div class="abs center" style="left:0;right:0;top:323px;font-size:3.4px">© 2024 BRVT Roofing. All rights reserved. &nbsp;&nbsp;<span style="color:var(--blue);text-decoration:underline">Privacy Policy</span> &nbsp;&nbsp;<span style="color:var(--blue);text-decoration:underline">Terms of Service</span> &nbsp;&nbsp;<span style="color:var(--blue);text-decoration:underline">Cookies Settings</span></div>
  </section>
</div>

</body>
</html>
```